Simple but elegant business card/logo design for exclusive beauty business

We need a logo designed for a new elegant and exclusive beauty business called "G". The logo itself should be a stylistic and custom design for the letter "G". We would like the business card to have the logo as the centrepiece on a clean background. Gold Logo on black background or silver on white background.

The business card details should be displayed centre of the card. Details are as follows:

Marla Vance
Facebook: /simplyshinebym
Instagram: /simplyshinebym

The words "Simply Shine" should also appear somewhere on the card.

Industry/Entity Type

Business

Logo Text

G

Requirements
Must have
• Design must be simple, clean and elegant
Should not have
• The design should not be cluttered

```html
<!DOCTYPE html>
<html lang="en">
<head>
<meta charset="utf-8">
<title>Marla Vance — Business Card</title>
<link href="https://fonts.googleapis.com/css2?family=Source+Sans+3:wght@400;600&family=Baloo+2:wght@600&display=swap" rel="stylesheet">
<style>
  :root {
    --stage: #484848;
    --card-light: #ffffff;
    --pattern-tint: #f6f6f3;
    --card-dark: #1e1f28;
    --accent: #e8901a;
    --ink: #2a2a2a;
    --rule: #b9b9b9;
  }
  html, body {
    margin: 0;
    padding: 0;
    width: 1200px;
    height: 900px;
    overflow: hidden;
    background: var(--stage);
  }
  .canvas {
    position: relative;
    width: 1200px;
    height: 900px;
  }
  .card {
    position: absolute;
    top: 306px;
    width: 439px;
    height: 271px;
    border-radius: 12px;
    overflow: hidden;
  }
  .card--front {
    left: 149px;
    background: var(--card-light);
  }
  .card--back {
    left: 609px;
    background: var(--card-dark);
  }
  .card__pattern {
    position: absolute;
    inset: 0;
    background: var(--pattern-tint);
  }
  .card__details {
    position: absolute;
    inset: 0;
    display: flex;
    flex-direction: column;
    align-items: center;
  }
  .holder-name {
    margin: 58px 0 0;
    font-family: "Source Sans 3", sans-serif;
    font-weight: 600;
    font-size: 20px;
    letter-spacing: 0.2px;
    color: var(--accent);
    text-transform: uppercase;
    line-height: 1;
  }
  .divider {
    width: 115px;
    height: 1px;
    margin-top: 14px;
    background: var(--rule);
  }
  .social-marks {
    display: flex;
    gap: 8px;
    margin-top: 19px;
  }
  .social-marks__dot {
    width: 23px;
    height: 23px;
    border-radius: 50%;
    background: var(--accent);
  }
  .social-handle {
    margin-top: 5px;
    font-family: "Source Sans 3", sans-serif;
    font-weight: 400;
    font-size: 16px;
    color: var(--ink);
    line-height: 1.2;
  }
  .tagline {
    margin-top: 18px;
    font-family: "Baloo 2", sans-serif;
    font-weight: 600;
    font-size: 31px;
    color: var(--accent);
    line-height: 1.2;
  }
  .brand-name {
    position: absolute;
    inset: 0;
    display: flex;
    align-items: center;
    justify-content: center;
    font-family: "Source Sans 3", sans-serif;
    font-weight: 600;
    font-size: 44px;
    color: var(--accent);
  }
</style>
</head>
<body>
<main class="canvas">
  <section class="card card--front">
    <div class="card__pattern" role="img" aria-label="Faint repeating brand monogram pattern"></div>
    <div class="card__details">
      <h1 class="holder-name">Marla Vance</h1>
      <div class="divider"></div>
      <div class="social-marks" aria-hidden="true">
        <span class="social-marks__dot"></span>
        <span class="social-marks__dot"></span>
      </div>
      <p class="social-handle" style="margin-bottom:0">/simplyshinebym</p>
      <p class="tagline" style="margin-bottom:0">Simply Shine</p>
    </div>
  </section>
  <section class="card card--back">
    <div class="brand-name">Maven</div>
  </section>
</main>
</body>
</html>
```